Business Card Design

We are a commercial real estate brokerage in San Francisco, leasing office buildings downtown.
I would like a clean, elegant look. Simple but powerful .

Industry/Entity Type

Business

Contact Information for Business Card

Derek Holloway
lic# 07258143
415.555.0172
derek@velt-commercial.example
velt-commercial.example

```html
<!DOCTYPE html>
<html lang="en">
<head>
<meta charset="UTF-8">
<title>VELT Commercial – Business Card</title>
<link href="https://fonts.googleapis.com/css2?family=Jost:wght@500;600&family=Open+Sans:wght@400;600&display=swap" rel="stylesheet">
<style>
  :root {
    --backdrop: #e6e6e4;
    --card: #f3f3f1;
    --brand: #5a6e8c;
    --ink: #2f3236;
    --muted: #55585c;
    --band: #5c5f63;
    --band-text: #e9e9e9;
  }
  * { margin: 0; padding: 0; box-sizing: border-box; }
  html, body {
    width: 1200px; height: 768px; overflow: hidden;
    background: var(--backdrop);
  }
  .stage {
    width: 1200px; height: 768px;
    display: flex; align-items: center; justify-content: center; gap: 60px;
  }
  .card {
    position: relative;
    width: 525px; height: 300px;
    background: var(--card);
    box-shadow: 0 6px 18px rgba(0,0,0,0.18);
    overflow: hidden;
  }
  .wordmark {
    display: flex; align-items: center; gap: 14px;
    font-family: "Jost", sans-serif; font-weight: 600;
    color: var(--brand); text-transform: uppercase; line-height: 0.95;
  }
  .wordmark-square {
    width: 44px; height: 44px; background: var(--brand); flex: none;
  }
  .wordmark-name { font-size: 44px; letter-spacing: 1px; }
  .wordmark-name span { display: block; font-size: 25px; letter-spacing: 1.5px; }

  .card--front { display: flex; align-items: center; justify-content: center; }

  .card--back .holder { position: absolute; left: 34px; top: 30px; }
  .holder-name {
    font-family: "Jost", sans-serif; font-weight: 600;
    font-size: 20px; color: var(--ink);
  }
  .holder-title {
    font-family: "Open Sans", sans-serif; font-size: 10.5px;
    color: var(--muted); margin-top: 3px;
  }
  .card--back .wordmark { position: absolute; right: 34px; top: 108px; }
  .card--back .wordmark-square { width: 34px; height: 34px; }
  .card--back .wordmark-name { font-size: 36px; }
  .card--back .wordmark-name span { font-size: 20px; }

  .contact {
    position: absolute; left: 34px; top: 185px;
    list-style: none;
    font-family: "Open Sans", sans-serif; font-size: 12px; color: var(--ink);
  }
  .contact li { display: flex; align-items: center; gap: 9px; height: 19px; }
  .contact svg { width: 12px; height: 12px; fill: var(--muted); flex: none; }

  .licence-band { position: absolute; right: 0; bottom: 22px; width: 250px; height: 40px; }
  .licence-band svg { position: absolute; inset: 0; }
  .licence-number {
    position: absolute; right: 26px; top: 0; line-height: 40px;
    font-family: "Open Sans", sans-serif; font-size: 13px;
    color: var(--band-text); letter-spacing: 0.5px;
  }
</style>
</head>
<body>
  <main class="stage">
    <section class="card card--front" aria-label="Card front">
      <div class="wordmark">
        <div class="wordmark-square"></div>
        <div class="wordmark-name">Velt<span>Commercial</span></div>
      </div>
    </section>

    <section class="card card--back" aria-label="Card back">
      <div class="holder">
        <h1 class="holder-name">Derek Holloway</h1>
        <p class="holder-title">Managing Director</p>
      </div>

      <div class="wordmark">
        <div class="wordmark-square"></div>
        <div class="wordmark-name">Velt<span>Commercial</span></div>
      </div>

      <ul class="contact">
        <li>
          <svg viewBox="0 0 24 24" aria-hidden="true"><path d="M6.6 10.8a15.1 15.1 0 0 0 6.6 6.6l2.2-2.2c.3-.3.7-.4 1-.2 1.1.4 2.3.6 3.6.6.6 0 1 .4 1 1V20c0 .6-.4 1-1 1A17 17 0 0 1 3 4c0-.6.4-1 1-1h3.5c.6 0 1 .4 1 1 0 1.3.2 2.5.6 3.6.1.3 0 .7-.2 1z"/></svg>
          415.555.0172
        </li>
        <li>
          <svg viewBox="0 0 24 24" aria-hidden="true"><path d="M2 5h20v14H2zm2 2v.5l8 5 8-5V7l-8 5z"/></svg>
          derek@velt-commercial.example
        </li>
        <li>
          <svg viewBox="0 0 24 24" aria-hidden="true"><path d="M12 2a10 10 0 1 0 0 20 10 10 0 0 0 0-20zm6.9 9h-3a15 15 0 0 0-1.3-5.6A8 8 0 0 1 18.9 11zM12 4.1c.9 1.2 1.8 3.6 1.9 6.9h-3.8c.1-3.3 1-5.7 1.9-6.9zM9.4 5.4A15 15 0 0 0 8.1 11h-3a8 8 0 0 1 4.3-5.6zM5.1 13h3a15 15 0 0 0 1.3 5.6A8 8 0 0 1 5.1 13zm6.9 6.9c-.9-1.2-1.8-3.6-1.9-6.9h3.8c-.1 3.3-1 5.7-1.9 6.9zm2.6-1.3a15 15 0 0 0 1.3-5.6h3a8 8 0 0 1-4.3 5.6z"/></svg>
          www.velt-commercial.example
        </li>
      </ul>

      <div class="licence-band">
        <svg viewBox="0 0 250 40" preserveAspectRatio="none" aria-hidden="true">
          <polygon points="0,0 250,0 250,40 22,40" fill="var(--band)"/>
        </svg>
        <span class="licence-number">LIC# 07258143</span>
      </div>
    </section>
  </main>
</body>
</html>
```